Automotive eCommerce Business looking for a business card design

Looking for a clean and simple business card design. Our company name is "Brindle Auto" and we are a company specializing in the ecommerce sales of automotive parts, specifically for pick up trucks and large SUVs. Our company colours are red, black, and white.

Feel free to use the logo provided or create a new logo that you seem fit. Looking forward to your creative ideas!

Industry/Entity Type

Automotive

Contact Information for Business Card

We were thinking of a possibly two-sided design featuring just the logo and company name on one side, and personal information on the other side. Single sided designs will be considered as well.

Font styles to use
Serif
Sans Serif
Decorative

Colors
ec1f27
ffffff
000000

Requirements
Must have
• Space for employee's name, title, phone number and email address, along with the company address and website somewhere.

```html
<!DOCTYPE html>
<html lang="en">
<head>
<meta charset="utf-8">
<title>Brindle Auto – Business Card</title>
<link href="https://fonts.googleapis.com/css2?family=Oswald:wght@500;700&family=Cinzel:wght@400&family=Roboto+Condensed:wght@400&display=swap" rel="stylesheet">
<style>
  :root {
    --brand-red: #a01d22;
    --brand-red-deep: #8e1a1f;
    --paper: #ffffff;
    --ink: #2b2b2b;
    --ink-soft: #6b6b6b;
    --backdrop: #e9e9e9;
  }
  * { box-sizing: border-box; margin: 0; padding: 0; }
  html, body { width: 1200px; height: 886px; overflow: hidden; }
  body {
    background: var(--backdrop);
    position: relative;
    font-family: "Roboto Condensed", Arial, sans-serif;
  }

  .card {
    position: absolute;
    border-radius: 22px;
    overflow: hidden;
    box-shadow: 0 10px 30px rgba(0,0,0,0.18);
  }

  /* ---------- Back side ---------- */
  .card-back {
    left: 90px; top: 273px;
    width: 600px; height: 340px;
    background: var(--brand-red);
    color: var(--paper);
  }
  .card-back .brand-lockup {
    position: absolute;
    left: 0; right: 0; top: 118px;
    display: flex; align-items: center; justify-content: center; gap: 14px;
  }
  .card-back .brand-mark {
    width: 22px; height: 22px; background: var(--paper);
  }
  .card-back .brand-name {
    font-family: "Oswald", Arial, sans-serif;
    font-weight: 500;
    font-size: 52px;
    letter-spacing: 2px;
    text-transform: uppercase;
    color: var(--paper);
  }
  .card-back .website {
    position: absolute;
    left: 0; right: 0; bottom: 44px;
    text-align: center;
    font-size: 15px;
    letter-spacing: 9px;
  }

  /* ---------- Front side ---------- */
  .card-front {
    left: 770px; top: 143px;
    width: 340px; height: 600px;
    background: var(--paper);
  }
  .card-front .red-field {
    position: absolute; inset: 0;
  }
  .card-front .brand-lockup {
    position: absolute;
    left: 34px; top: 70px;
    display: flex; align-items: center; gap: 10px;
  }
  .card-front .brand-mark {
    width: 18px; height: 18px; background: var(--brand-red);
  }
  .card-front .brand-name {
    font-family: "Oswald", Arial, sans-serif;
    font-weight: 500;
    font-size: 34px;
    letter-spacing: 1px;
    text-transform: uppercase;
    color: var(--brand-red);
  }
  .card-front .company-line {
    position: absolute;
    left: 36px; top: 160px;
    font-family: "Cinzel", Georgia, serif;
    font-size: 22px;
    color: var(--ink-soft);
  }
  .card-front .person {
    position: absolute;
    left: 36px; top: 214px;
  }
  .person-name {
    font-family: "Oswald", Arial, sans-serif;
    font-weight: 700;
    font-size: 30px;
    line-height: 1;
    color: var(--brand-red);
    text-transform: uppercase;
  }
  .person-title {
    margin-top: 6px;
    font-size: 17px;
    color: var(--ink);
    text-transform: uppercase;
  }

  .card-front .contact {
    position: absolute;
    left: 36px; bottom: 44px;
    color: var(--paper);
    font-size: 17px;
    line-height: 1.35;
  }
  .address { margin-bottom: 16px; }
  .contact-list { list-style: none; }
  .contact-list li { display: flex; align-items: center; gap: 8px; }
  .contact-list svg { width: 14px; height: 14px; fill: var(--paper); flex: none; }
</style>
</head>
<body>

  <section class="card card-back" aria-label="Business card, back">
    <div class="brand-lockup">
      <span class="brand-mark"></span>
      <span class="brand-name">Brindle Auto</span>
    </div>
    <p class="website">www.brindleparts.com</p>
  </section>

  <section class="card card-front" aria-label="Business card, front">
    <svg class="red-field" viewBox="0 0 340 600" preserveAspectRatio="none" aria-hidden="true">
      <polygon points="0,600 0,352 120,352 260,300 340,318 340,600" fill="var(--brand-red)"/>
    </svg>

    <div class="brand-lockup">
      <span class="brand-mark"></span>
      <span class="brand-name">Brindle Auto</span>
    </div>
    <p class="company-line">Brindle Auto Ltd.</p>

    <div class="person">
      <p class="person-name">Dana Whitlock</p>
      <p class="person-title">CEO/Founder</p>
    </div>

    <div class="contact">
      <p class="address">4120 Alder Crest Road<br>Juneau, Alaska 99801</p>
      <ul class="contact-list">
        <li>
          <svg viewBox="0 0 16 16" aria-hidden="true"><path d="M3.5 1.5l2.2 2.6-1.3 1.7c.9 1.9 2.3 3.3 4.2 4.2l1.7-1.3 2.6 2.2-1.2 2.4C6.6 13 3 9.4 1.1 2.7z"/></svg>
          907 512 4470
        </li>
        <li>
          <svg viewBox="0 0 16 16" aria-hidden="true"><path d="M4.5 1h7v14h-7zM5.8 2.5v9.5h4.4V2.5zM7.3 13h1.4v1H7.3z" fill-rule="evenodd"/></svg>
          907 318 2265
        </li>
        <li>
          <svg viewBox="0 0 16 16" aria-hidden="true"><path d="M4 1h6l2 2v3h2v8H2V6h2zM5 2.2V6h6V3.4L9.6 2.2zM4 9h8v1H4zm0 2h8v1H4z" fill-rule="evenodd"/></svg>
          907 512 4471
        </li>
        <li>
          <svg viewBox="0 0 16 16" aria-hidden="true"><path d="M1 3h14v10H1zm1.5 1.3v.4L8 8.6l5.5-3.9v-.4zM2.5 6.4v5.3h11V6.4L8 10.3z" fill-rule="evenodd"/></svg>
          dana@brindleparts.com
        </li>
        <li>
          <svg viewBox="0 0 16 16" aria-hidden="true"><path d="M8 1a7 7 0 100 14A7 7 0 008 1zm0 1.4c.9 0 1.8 1.8 2 4.6H6c.2-2.8 1.1-4.6 2-4.6zM2.5 7h2.1c.1-1.7.4-3.1 1-4A5.6 5.6 0 002.5 7zm0 1.5a5.6 5.6 0 003.1 4c-.6-.9-.9-2.3-1-4zm3.5 0h4c-.2 2.8-1.1 4.6-2 4.6s-1.8-1.8-2-4.6zm5.4 0c-.1 1.7-.4 3.1-1 4a5.6 5.6 0 003.1-4zm2.1-1.5a5.6 5.6 0 00-3.1-4c.6.9.9 2.3 1 4z" fill-rule="evenodd"/></svg>
          www.brindleparts.com
        </li>
      </ul>
    </div>
  </section>

</body>
</html>
```